Responsive OnePage Design for recruitment company

Corvanta is a modern company that sources interim people for its customers. Mostly developers, scrum master, project managers and designers. In this website we want to tell something about us, about how we work, our customers and we want our candidates be able to subscribe. The subscription form should be several fields (name, surname, email address, phone number and the possibility to upload your resume.We want it to fit into a existing wordpress plugin. We also want a listing of our job opportunities. The listing should be designed in a clear readable overview and if you click on the job you should get the details and be able to respond quickly by filling in you name, surname, email address, rate, phone number and upload your resume. We want this to be a standard configurable plugin. It should be easy to fill in the jobs in Wordpress by our administrator. We want a fresh, modern and cool design. It should be a responsive onepage design. If you click on a listed job you should stay on the same page. Our logo is added.

Target Market(s)

recruitment

Industry/Entity Type

Recruitment

Font styles to use
Sans Serif

Colors

Designer to choose colors to be used in the design.

Requirements
Must have
• Onepage design
• listing of job opportunities
• subscription forms
• be responsive

```html
<!DOCTYPE html>
<html lang="en">
<head>
<meta charset="utf-8">
<title>Corvanta — Interim Recruitment</title>
<link rel="stylesheet" href="https://fonts.googleapis.com/css2?family=Montserrat:wght@400;500;600;700&family=Open+Sans:wght@400;600&display=swap">
<style>
:root{
  --blue:#1478c8;
  --blue-dark:#0b3f8c;
  --ink:#2b2b2b;
  --text:#555;
  --muted:#8a8a8a;
  --line:#e2e2e2;
  --grey-band:#ececec;
  --grey-soft:#f6f6f6;
  --red:#e2445c;
}
*{margin:0;padding:0;box-sizing:border-box}
html,body{width:1200px;height:4036px;overflow:hidden}
body{position:relative;background:#fff;font-family:"Open Sans",Arial,sans-serif;color:var(--text)}
.abs{position:absolute}
h2,h3,.nav,.brand{font-family:"Montserrat",Arial,sans-serif}

.brand{left:174px;top:30px;font-size:21px;font-weight:600;letter-spacing:4px;color:var(--ink)}
.nav{top:37px;right:175px;display:flex;gap:26px;font-size:12.5px;font-weight:600;color:var(--ink);text-transform:uppercase}
.nav .active{color:var(--blue)}

.hero{left:0;top:85px;width:1200px;height:645px;clip-path:polygon(0 0,100% 0,100% 84.6%,0 100%);
  background:linear-gradient(100deg,#c9cdd3 0%,#8e98a6 35%,#4a5566 55%,#d8dbe0 80%,#eef0f2 100%)}
.hero-box{left:162px;top:296px;width:420px;height:200px;background:rgba(40,40,40,.78)}
.hero-title{left:176px;top:338px;font-family:"Montserrat",Arial,sans-serif;font-weight:700;font-size:32px;line-height:46px;color:#fff}
.dots{left:512px;top:636px;display:flex;gap:6px}
.dots span{width:40px;height:4px;background:rgba(255,255,255,.6)}
.dots span.on{background:#fff}

.sec-title{font-size:32px;font-weight:500;color:var(--ink)}
.sec-title em{font-style:normal;color:var(--blue)}
.rule{width:80px;height:3px;background:var(--blue)}
.center{left:0;width:1200px;text-align:center}
.intro{left:330px;width:540px;text-align:center;font-size:12.5px;line-height:21px;color:var(--text)}

.about-text{left:174px;top:880px;width:370px;font-size:12.5px;line-height:21.5px}
.about-media{left:575px;top:795px;width:448px;height:340px;box-shadow:10px 10px 0 var(--blue-dark);
  background:linear-gradient(135deg,#b9d3ea,#6f97bf 45%,#e7eef5)}
.play{left:775px;top:938px;width:60px;height:60px;border:3px solid #fff;border-radius:50%}
.play:after{content:"";position:absolute;left:22px;top:16px;border-left:18px solid #fff;border-top:11px solid transparent;border-bottom:11px solid transparent}

.how-band{left:0;top:1240px;width:1200px;height:680px;background:var(--grey-band);clip-path:polygon(0 0,100% 6%,100% 100%,0 90%)}
.steps-line{left:263px;top:1584px;width:674px;border-top:2px dashed #b7b7b7}
.step{width:200px;text-align:center}
.step .icon{margin:0 auto;width:98px;height:98px;border-radius:50%;border:4px solid var(--blue);background:#fff;padding:6px}
.step .icon i{display:block;width:100%;height:100%;border-radius:50%;background:radial-gradient(circle,#f4c56a,#e56b3d 55%,#2f6fb0)}
.step h3{margin-top:18px;font-size:15px;font-weight:600;color:var(--ink)}
.step p{margin-top:12px;font-size:12px;line-height:20px}

.job{left:172px;width:855px;height:64px;border:1px solid var(--line);background:#fff;box-shadow:0 1px 3px rgba(0,0,0,.05)}
.job h4{position:absolute;left:24px;top:14px;font-family:"Montserrat",Arial,sans-serif;font-size:15px;font-weight:600;color:var(--ink)}
.job small{position:absolute;left:24px;top:36px;font-size:11px;color:var(--muted)}
.job .loc{position:absolute;left:470px;top:24px;font-size:11.5px;color:var(--muted);display:flex;align-items:center;gap:8px}
.job .tag{position:absolute;right:42px;top:16px;width:92px;height:30px;border-radius:15px;border:1.5px solid var(--blue);color:var(--blue);font-size:11px;font-weight:700;text-align:center;line-height:27px;font-family:"Montserrat",Arial,sans-serif}
.job .tag.part{border-color:var(--red);color:var(--red)}
.pager{left:525px;top:2684px;display:flex;gap:8px}
.pager span{width:32px;height:32px;border:1.5px solid var(--line);border-radius:50%;text-align:center;line-height:29px;font-size:12px;color:var(--ink)}
.pager span.on{border-color:var(--blue);color:var(--blue)}

.cust-band{left:0;top:2790px;width:1200px;height:560px;background:var(--grey-soft);clip-path:polygon(0 0,100% 11%,100% 100%,0 100%)}
.logos{left:300px;width:600px;display:flex;justify-content:space-around;align-items:center;font-family:"Montserrat",Arial,sans-serif;font-size:22px;font-weight:600;color:#6d6d6d}

.contact-bg{left:0;top:3320px;width:1200px;height:525px;clip-path:polygon(0 0,100% 12%,100% 100%,0 100%);
  background:linear-gradient(100deg,#3a2a22 0%,#1c1816 45%,#2b2420 70%,#4a3b33 100%)}
.touch{left:172px;top:3464px;color:#fff}
.touch h3{font-size:22px;font-weight:600}
.touch .rule{width:55px;margin-top:12px}
.touch dl{margin-top:30px;font-size:13px;line-height:21px}
.touch dt{font-weight:600;display:flex;align-items:center;gap:14px}
.touch dd{margin:2px 0 22px 24px}
.sub{left:610px;top:3355px;width:415px;height:525px;background:linear-gradient(180deg,#1a93d6,#0b3a8a);box-shadow:0 10px 25px rgba(0,0,0,.35)}
.sub h3{margin-top:32px;text-align:center;font-size:36px;font-weight:500;color:#fff}
.field{position:absolute;left:38px;width:345px;height:38px;border:1.5px solid rgba(255,255,255,.7);border-radius:19px;color:#fff;font-size:13px;padding:10px 18px}
.field.area{height:84px;border-radius:18px}
.field svg{position:absolute;right:14px;top:11px}
.submit{position:absolute;left:38px;top:440px;width:345px;height:40px;border-radius:20px;background:#fff;color:var(--blue-dark);text-align:center;line-height:40px;font-family:"Montserrat",Arial,sans-serif;font-size:13px;font-weight:700}

.social{left:532px;top:3928px;display:flex;gap:8px}
.social span{width:40px;height:38px;background:#2c2c2c}
.copy{left:0;width:1200px;top:3988px;text-align:center;font-size:13px;color:var(--ink)}
</style>
</head>
<body>

<header>
  <div class="abs brand">CORVANTA</div>
  <nav class="abs nav"><span class="active">Home</span><span>About</span><span>How we work</span><span>Job opportunities</span><span>Customers</span><span>Contact</span></nav>
</header>

<section class="hero-section">
  <div class="abs hero" role="img" aria-label="Photo of a recruiter in a suit meeting a candidate in a bright office"></div>
  <div class="abs hero-box"></div>
  <h1 class="abs hero-title">Find Your Dream Job.<br>Move up Today</h1>
  <div class="abs dots"><span class="on"></span><span class="on"></span><span></span><span></span></div>
</section>

<section class="about">
  <h2 class="abs sec-title" style="left:174px;top:815px">About <em>Corvanta</em></h2>
  <div class="abs rule" style="left:174px;top:862px"></div>
  <p class="abs about-text">We connect skilled interim professionals with companies that need them fast. Our team listens closely to each client, learns how their projects run and finds people who fit the work and the culture. From developers and scrum masters to project managers and designers, we match talent with care. Candidates get honest advice, quick feedback and a partner who keeps looking out for their next step long after the first placement is done. We keep every process simple, open and personal.</p>
  <div class="abs about-media" role="img" aria-label="Video still of a team working together around laptops"></div>
  <div class="abs play"></div>
</section>

<section class="how">
  <div class="abs how-band"></div>
  <h2 class="abs sec-title center" style="top:1372px">How <em>We Work</em></h2>
  <div class="abs rule" style="left:560px;top:1418px"></div>
  <p class="abs intro" style="top:1438px">Four simple steps take you from first visit to your next interim role. Sign up, build your profile, browse open jobs and apply in minutes.</p>
  <div class="abs steps-line"></div>
  <div class="abs step" style="left:163px;top:1535px"><div class="icon"><i role="img" aria-label="Illustration of a clipboard and pencil"></i></div><h3>REGISTER</h3><p>Create a free account in a few clicks and join our growing network of interim experts.</p></div>
  <div class="abs step" style="left:387px;top:1535px"><div class="icon"><i role="img" aria-label="Illustration of a person in business wear"></i></div><h3>UPLOAD PROFILE</h3><p>Add your skills, experience and rate so we can match you with the right roles.</p></div>
  <div class="abs step" style="left:612px;top:1535px"><div class="icon"><i role="img" aria-label="Illustration of a magnifying glass"></i></div><h3>SEARCH JOBS</h3><p>Filter open positions by role, location and contract type to find the work you want.</p></div>
  <div class="abs step" style="left:837px;top:1535px"><div class="icon"><i role="img" aria-label="Illustration of a paper plane"></i></div><h3>APPLY JOBS</h3><p>Send your details and resume straight from the job page and hear back from us quickly.</p></div>
</section>

<section class="jobs">
  <h2 class="abs sec-title center" style="top:1982px">Job <em>Opportunities</em></h2>
  <div class="abs rule" style="left:560px;top:2028px"></div>
  <p class="abs intro" style="top:2048px">Browse our latest interim assignments below. Click any job to see the full details and respond right away with your rate and resume.</p>

  <div class="abs job" style="top:2119px"><h4>Developers</h4><small>Interim role, start soon, remote options</small><span class="loc"><svg width="9" height="12" viewBox="0 0 9 12"><path d="M4.5 0A4.5 4.5 0 0 0 0 4.5C0 8 4.5 12 4.5 12S9 8 9 4.5A4.5 4.5 0 0 0 4.5 0zm0 6.3a1.8 1.8 0 1 1 0-3.6 1.8 1.8 0 0 1 0 3.6z" fill="#888"/></svg>Location Name, City Name</span><span class="tag">FULL TIME</span></div>
  <div class="abs job" style="top:2194px"><h4>Scrum master</h4><small>Interim role, agile team, long project</small><span class="loc"><svg width="9" height="12" viewBox="0 0 9 12"><path d="M4.5 0A4.5 4.5 0 0 0 0 4.5C0 8 4.5 12 4.5 12S9 8 9 4.5A4.5 4.5 0 0 0 4.5 0zm0 6.3a1.8 1.8 0 1 1 0-3.6 1.8 1.8 0 0 1 0 3.6z" fill="#888"/></svg>Location Name, City Name</span><span class="tag part">PART TIME</span></div>
  <div class="abs job" style="top:2269px"><h4>Project managers</h4><small>Interim role, large client, quick start</small><span class="loc"><svg width="9" height="12" viewBox="0 0 9 12"><path d="M4.5 0A4.5 4.5 0 0 0 0 4.5C0 8 4.5 12 4.5 12S9 8 9 4.5A4.5 4.5 0 0 0 4.5 0zm0 6.3a1.8 1.8 0 1 1 0-3.6 1.8 1.8 0 0 1 0 3.6z" fill="#888"/></svg>Location Name, City Name</span><span class="tag">FULL TIME</span></div>
  <div class="abs job" style="top:2344px"><h4>Developers</h4><small>Interim role, backend work, hybrid setup</small><span class="loc"><svg width="9" height="12" viewBox="0 0 9 12"><path d="M4.5 0A4.5 4.5 0 0 0 0 4.5C0 8 4.5 12 4.5 12S9 8 9 4.5A4.5 4.5 0 0 0 4.5 0zm0 6.3a1.8 1.8 0 1 1 0-3.6 1.8 1.8 0 0 1 0 3.6z" fill="#888"/></svg>Location Name, City Name</span><span class="tag part">PART TIME</span></div>
  <div class="abs job" style="top:2419px"><h4>Scrum master</h4><small>Interim role, two teams, flexible hours</small><span class="loc"><svg width="9" height="12" viewBox="0 0 9 12"><path d="M4.5 0A4.5 4.5 0 0 0 0 4.5C0 8 4.5 12 4.5 12S9 8 9 4.5A4.5 4.5 0 0 0 4.5 0zm0 6.3a1.8 1.8 0 1 1 0-3.6 1.8 1.8 0 0 1 0 3.6z" fill="#888"/></svg>Location Name, City Name</span><span class="tag">FULL TIME</span></div>
  <div class="abs job" style="top:2495px"><h4>Designers</h4><small>Interim role, product design, creative team</small><span class="loc"><svg width="9" height="12" viewBox="0 0 9 12"><path d="M4.5 0A4.5 4.5 0 0 0 0 4.5C0 8 4.5 12 4.5 12S9 8 9 4.5A4.5 4.5 0 0 0 4.5 0zm0 6.3a1.8 1.8 0 1 1 0-3.6 1.8 1.8 0 0 1 0 3.6z" fill="#888"/></svg>Location Name, City Name</span><span class="tag">FULL TIME</span></div>
  <div class="abs job" style="top:2570px"><h4>Project managers</h4><small>Interim role, public sector, six months</small><span class="loc"><svg width="9" height="12" viewBox="0 0 9 12"><path d="M4.5 0A4.5 4.5 0 0 0 0 4.5C0 8 4.5 12 4.5 12S9 8 9 4.5A4.5 4.5 0 0 0 4.5 0zm0 6.3a1.8 1.8 0 1 1 0-3.6 1.8 1.8 0 0 1 0 3.6z" fill="#888"/></svg>Location Name, City Name</span><span class="tag part">PART TIME</span></div>

  <div class="abs pager"><span class="on">1</span><span>2</span><span>3</span><span>4</span></div>
</section>

<section class="customers">
  <div class="abs cust-band"></div>
  <h2 class="abs sec-title center" style="top:2926px">Our <em>Customers</em></h2>
  <div class="abs rule" style="left:560px;top:2972px"></div>
  <p class="abs intro" style="top:2992px">Leading firms across many sectors trust us to find the interim talent that keeps their projects moving and their teams strong.</p>
  <div class="abs logos" style="top:3086px"><span>Tolvek</span><span>Brennick</span><span>Oslund</span><span>Mavero</span></div>
  <div class="abs logos" style="top:3176px;font-size:18px"><span>Hollowby</span><span>Ferncastle</span><span>Varnel</span><span>Gessmoor</span></div>
</section>

<section class="contact">
  <div class="abs contact-bg" role="img" aria-label="Dark photo of two people shaking hands"></div>
  <div class="abs touch">
    <h3>Get In Touch</h3>
    <div class="rule"></div>
    <dl>
      <dt><svg width="10" height="13" viewBox="0 0 9 12"><path d="M4.5 0A4.5 4.5 0 0 0 0 4.5C0 8 4.5 12 4.5 12S9 8 9 4.5A4.5 4.5 0 0 0 4.5 0zm0 6.3a1.8 1.8 0 1 1 0-3.6 1.8 1.8 0 0 1 0 3.6z" fill="#fff"/></svg>Address:</dt>
      <dd>48 Maple Row<br>Fairvale, TX 75410</dd>
      <dt><svg width="11" height="11" viewBox="0 0 24 24"><path d="M6.6 10.8a15 15 0 0 0 6.6 6.6l2.2-2.2c.3-.3.7-.4 1-.2 1.1.4 2.3.6 3.6.6.6 0 1 .4 1 1V20c0 .6-.4 1-1 1A17 17 0 0 1 3 4c0-.6.4-1 1-1h3.5c.6 0 1 .4 1 1 0 1.3.2 2.5.6 3.6.1.3 0 .7-.2 1z" fill="#fff"/></svg>Phone Number:</dt>
      <dd>Phone: (555) 018-4427</dd>
      <dt><svg width="12" height="10" viewBox="0 0 24 18"><path d="M0 0h24v18H0z" fill="#fff"/><path d="M0 0l12 9 12-9" fill="none" stroke="#2b2420" stroke-width="2"/></svg>Email Address:</dt>
      <dd>hello@corvanta.example</dd>
    </dl>
  </div>
  <form class="abs sub">
    <h3>Subscription</h3>
    <div class="field" style="top:100px">Name</div>
    <div class="field" style="top:147px">Surname</div>
    <div class="field" style="top:194px">Email</div>
    <div class="field" style="top:241px">Phone</div>
    <div class="field area" style="top:288px">Address</div>
    <div class="field" style="top:388px">Upload your resume<svg width="14" height="14" viewBox="0 0 14 14"><path d="M7 0v8M3 4l4-4 4 4M1 10v3h12v-3" fill="none" stroke="#fff" stroke-width="2"/></svg></div>
    <div class="submit">SUBMIT HERE</div>
  </form>
</section>

<footer>
  <div class="abs social"><span aria-label="Social link one"></span><span aria-label="Social link two"></span><span aria-label="Social link three"></span></div>
  <p class="abs copy">© 2019 Corvanta, All Rights Are Reserved Terms of Use | Privacy Policy</p>
</footer>

</body>
</html>
```